Pim Tavel Brochure Design

We are a Marketing company offering different services. Services must be outlined on design we will provive text for the services once project is accepted.

Service Titles to include in design

Corporate Branding
Marketing
Web Design 
Business Consultation
Printing
Mailing
Automation
Pim Tavel Prime

Please post designs, we have n

Target Market(s)

18+ Years Old

Must have
• Web 2.0 Graphics
• Eye catching design
Nice to have
• Rich Graphics
• Creativity
Should not have
• Standard Templates
• Only bullets

```html
<!DOCTYPE html>
<html lang="en">
<head>
<meta charset="utf-8">
<title>Pim Tavel Marketing – Services Brochure</title>
<link href="https://fonts.googleapis.com/css2?family=Libre+Franklin:wght@400;800&display=swap" rel="stylesheet">
<style>
  :root {
    --bg-dark: #353535;
    --bg-mid: #424242;
    --orange: #f6a11c;
    --ink: #161616;
    --people: #2c2c2c;
  }
  * { margin: 0; padding: 0; box-sizing: border-box; }
  html, body { width: 1200px; height: 932px; overflow: hidden; background: var(--bg-dark); }
  .brochure {
    position: relative;
    width: 1200px;
    height: 932px;
    overflow: hidden;
    background: radial-gradient(circle at 55% 45%, var(--bg-mid), var(--bg-dark) 75%);
    font-family: "Libre Franklin", Arial, sans-serif;
    color: var(--ink);
  }
  .gears { position: absolute; inset: 0; }
  .team-photo {
    position: absolute;
    left: 24px;
    top: 625px;
    width: 240px;
    height: 290px;
    background: linear-gradient(180deg, #3c3c3c, var(--people));
    border-radius: 60px 60px 6px 6px;
    opacity: 0.8;
  }
  .service-group { position: absolute; text-align: center; }
  .service { margin: 0 auto 12px; }
  .service h2 {
    font-weight: 800;
    font-size: 14.5px;
    line-height: 17px;
  }
  .service p {
    font-weight: 400;
    font-size: 14.5px;
    line-height: 16.2px;
  }
  .group-left { left: 40px; top: 104px; width: 480px; }
  .group-left .branding { width: 330px; }
  .group-left .marketing { width: 455px; }
  .group-left .webdesign { width: 370px; }
  .group-right { left: 820px; top: 36px; width: 360px; }
  .group-right .mailing { width: 330px; }
  .group-right .automation { width: 350px; }
  .group-right .prime { width: 320px; }
  .group-center { left: 502px; top: 454px; width: 400px; }
  .group-center .service { margin-bottom: 14px; }
  .group-center .service h2,
  .group-center .service p { font-size: 15px; }
  .group-center .service p { line-height: 17.4px; }
  .group-center .consult { width: 330px; }
  .group-center .printing { width: 380px; }
  .brand-mark {
    position: absolute;
    right: 36px;
    bottom: 52px;
    display: flex;
    align-items: center;
    gap: 12px;
  }
  .brand-mark .dot {
    width: 26px; height: 26px; border-radius: 50%;
    background: var(--orange);
  }
  .brand-mark .name {
    font-weight: 800;
    font-size: 36px;
    letter-spacing: 1px;
    color: var(--orange);
  }
</style>
</head>
<body>
<main class="brochure">
  <svg class="gears" width="1200" height="932" viewBox="0 0 1200 932" aria-hidden="true">
    <defs>
      <linearGradient id="grad-silver-orange" gradientUnits="userSpaceOnUse" x1="0" y1="-1" x2="0" y2="1">
        <stop offset="0" stop-color="#d4d2d0"/>
        <stop offset="0.55" stop-color="#e2b36a"/>
        <stop offset="1" stop-color="#f7990f"/>
      </linearGradient>
      <linearGradient id="grad-orange-silver" gradientUnits="userSpaceOnUse" x1="0" y1="-1" x2="0" y2="1">
        <stop offset="0" stop-color="#f6a72a"/>
        <stop offset="0.5" stop-color="#e7c08a"/>
        <stop offset="1" stop-color="#d0cdca"/>
      </linearGradient>
    </defs>

    <g class="gear gear-team" transform="translate(40 850) scale(318)">
      <circle r="0.82" fill="url(#grad-orange-silver)"/>
      <circle r="0.9" fill="none" stroke="url(#grad-orange-silver)" stroke-width="0.2" stroke-dasharray="0.2 0.27124" stroke-dashoffset="0.05"/>
    </g>

    <g class="gear gear-center" transform="translate(702 630) scale(290)">
      <circle r="0.82" fill="url(#grad-orange-silver)"/>
      <circle r="0.9" fill="none" stroke="url(#grad-orange-silver)" stroke-width="0.2" stroke-dasharray="0.2 0.27124" stroke-dashoffset="0.1"/>
    </g>

    <g class="gear gear-right" transform="translate(1000 235) scale(310)">
      <circle r="0.82" fill="url(#grad-orange-silver)"/>
      <circle r="0.9" fill="none" stroke="url(#grad-orange-silver)" stroke-width="0.2" stroke-dasharray="0.2 0.27124" stroke-dashoffset="0.2"/>
    </g>

    <g class="gear gear-left" transform="translate(280 325) scale(320)">
      <circle r="0.82" fill="url(#grad-silver-orange)"/>
      <circle r="0.9" fill="none" stroke="url(#grad-silver-orange)" stroke-width="0.2" stroke-dasharray="0.2 0.27124" stroke-dashoffset="0.1"/>
    </g>
  </svg>

  <div class="team-photo" role="img" aria-label="Silhouettes of a business team standing together"></div>

  <section class="service-group group-left">
    <article class="service branding">
      <h2>CORPORATE BRANDING</h2>
      <p>Lorem ipsum dolor sit amet, consectetuer adipiscing elit. Nullam euismod mollis nisl. Morbi ultricies neque vel ipsum. Aenean cursus. Aenean elit. Aliquam commodo. Praesent quis ante in eros gravida blandit. Nullam sagittis. Ut eu urna in orci gravida sodales. Sed volutpat cursus nunc.</p>
    </article>
    <article class="service marketing">
      <h2>MARKETING</h2>
      <p>Lorem ipsum dolor sit amet, consectetuer adipiscing elit. Nullam euismod mollis nisl. Morbi ultricies neque vel ipsum. Aenean cursus. Aenean elit. Aliquam commodo. Praesent quis ante in eros gravida blandit. Nullam sagittis. Ut eu urna in orci gravida sodales. Sed volutpat cursus nunc. Mauris porta dolor quis lectus tincidunt congue. Mauris sed arcu id erat molestie laoreet.</p>
    </article>
    <article class="service webdesign">
      <h2>WEB DESIGN</h2>
      <p>Lorem ipsum dolor sit amet, consectetuer adipiscing elit. Nullam euismod mollis nisl. Morbi ultricies neque vel ipsum. Aenean cursus. Aenean elit. Aliquam commodo. Praesent quis ante in eros gravida blandit. Nullam sagittis. Ut eu urna in orci gravida sodales. Sed volutpat cursus nunc. Mauris porta dolor quis lectus tincidunt congue.</p>
    </article>
  </section>

  <section class="service-group group-right">
    <article class="service mailing">
      <h2>MAILING</h2>
      <p>Lorem ipsum dolor sit amet, consectetuer adipiscing elit. Nullam euismod mollis nisl. Morbi ultricies neque vel ipsum. Aenean cursus. Aenean elit. Aliquam commodo. Praesent quis ante in eros gravida blandit. Nullam sagittis.</p>
    </article>
    <article class="service automation">
      <h2>AUTOMATION</h2>
      <p>Lorem ipsum dolor sit amet, consectetuer adipiscing elit. Nullam euismod mollis nisl. Morbi ultricies neque vel ipsum. Aenean cursus. Aenean elit. Aliquam commodo. Praesent quis ante in eros gravida blandit. Nullam sagittis. Ut eu urna in orci gravida sodales. Sed volutpat cursus nunc.</p>
    </article>
    <article class="service prime">
      <h2>PIM TAVEL PRIME</h2>
      <p>Lorem ipsum dolor sit amet, consectetuer adipiscing elit. Nullam euismod mollis nisl. Morbi ultricies neque vel ipsum. Aenean cursus. Aenean elit. Aliquam commodo. Praesent quis ante in eros gravida blandit. Nullam sagittis. Mauris porta dolor quis lectus tincidunt congue.</p>
    </article>
  </section>

  <section class="service-group group-center">
    <article class="service consult">
      <h2>BUSINESS CONSULTATION</h2>
      <p>Lorem ipsum dolor sit amet, consectetuer adipiscing elit. Nullam euismod mollis nisl. Morbi ultricies neque vel ipsum. Aenean cursus. Aenean elit. Aliquam commodo. Praesent quis ante in eros gravida blandit. Nullam sagittis. Ut eu urna in orci gravida sodales. Sed volutpat cursus nunc. Mauris porta dolor quis lectus tincidunt congue. Mauris sed arcu id erat molestie laoreet.</p>
    </article>
    <article class="service printing">
      <h2>PRINTING</h2>
      <p>Lorem ipsum dolor sit amet, consectetuer adipiscing elit. Nullam euismod mollis nisl. Morbi ultricies neque vel ipsum. Aenean cursus. Aenean elit. Aliquam commodo. Praesent quis ante in eros gravida blandit. Nullam sagittis. Ut eu urna in orci gravida sodales. Sed volutpat cursus nunc. Mauris porta dolor quis lectus tincidunt congue. Mauris sed arcu id erat molestie laoreet.</p>
    </article>
  </section>

  <div class="brand-mark">
    <span class="dot"></span>
    <span class="name">PIM TAVEL</span>
  </div>
</main>
</body>
</html>
```